Business Card for premium dental clinic

We are a premium dental clinic based in Brasov, Romania with more than 15 year on the market, providing quality dental treatment made by a team of more specialized dentists, working with modern equipment as a solution to beautiful and healthy teeth.

Our current logo for the clinic use 2 square with colors black and gold - dr Ternisu - studio, using family fonts Bodoni, Myriad Pro and Segoe Print.
Depending on the printing we used some gold CMYK background or gold foil picture background or a gold gradient.
We want a business card:
- eye catching business card
- distinguished business card
- premium design
- to keep the color scheme of black and gold
- to attract the customers to spent time reading the information
- modern concept

```html
<!DOCTYPE html>
<html lang="en">
<head>
<meta charset="utf-8">
<title>dr Ternisu studio – business card</title>
<link rel="stylesheet" href="https://fonts.googleapis.com/css2?family=Open+Sans:wght@400;600&display=swap">
<style>
  :root {
    --page: #e4e4e4;
    --black: #050505;
    --white: #ffffff;
    --gold-dark: #b8860b;
    --gold: #d9a82a;
    --gold-light: #fbe27a;
    --ink: #111111;
  }
  html, body {
    margin: 0;
    width: 1200px;
    height: 1006px;
    overflow: hidden;
    background: var(--page);
  }
  .card {
    position: absolute;
    left: 100px;
    top: 218px;
    width: 1000px;
    height: 570px;
    box-sizing: border-box;
    padding: 22px;
    background: linear-gradient(135deg, var(--gold-dark) 0%, var(--gold-light) 30%, var(--gold) 55%, var(--gold-light) 78%, var(--gold-dark) 100%);
    box-shadow: 0 10px 24px rgba(0,0,0,0.25);
  }
  .card-face {
    position: relative;
    width: 100%;
    height: 100%;
    background: var(--white);
    overflow: hidden;
  }
  .black-panel {
    position: absolute;
    left: 0;
    top: 0;
    width: 39%;
    height: 100%;
    background: var(--black);
  }
  .gold-foil {
    position: absolute;
    left: 120px;
    top: 150px;
    width: 240px;
    height: 240px;
    border: 3px solid var(--white);
    background: radial-gradient(circle at 35% 35%, var(--gold-light) 0%, var(--gold) 50%, var(--gold-dark) 100%);
  }
  .brand-name {
    position: absolute;
    left: 0;
    width: 39%;
    top: 420px;
    margin: 0;
    text-align: center;
    font-family: "Open Sans", sans-serif;
    font-weight: 400;
    font-size: 34px;
    color: var(--white);
    letter-spacing: 0.5px;
  }
  .contact {
    position: absolute;
    left: 570px;
    top: 150px;
    font-family: "Open Sans", sans-serif;
    font-weight: 400;
    color: var(--ink);
  }
  .address {
    margin: 0 0 40px;
    font-size: 22px;
    line-height: 1.4;
  }
  .contact-list {
    list-style: none;
    margin: 0;
    padding: 0;
    font-size: 22px;
  }
  .contact-list li {
    display: flex;
    align-items: center;
    gap: 14px;
    height: 32px;
  }
  .contact-icon {
    width: 20px;
    height: 20px;
    flex: none;
    fill: none;
    stroke: var(--gold);
    stroke-width: 1.8;
  }
</style>
</head>
<body>
  <div class="card">
    <div class="card-face">
      <div class="black-panel"></div>
      <div class="gold-foil" role="img" aria-label="Gold foil texture square"></div>
      <p class="brand-name">dr Ternisu studio</p>

      <div class="contact">
        <p class="address">strada Lunga nr 8<br>Brasov, Romania 500035</p>
        <ul class="contact-list">
          <li>
            <svg class="contact-icon" viewBox="0 0 20 20" aria-hidden="true"><rect x="5" y="1.5" width="10" height="17" rx="1.5"/><line x1="9" y1="15.5" x2="11" y2="15.5"/></svg>
            +40 700 318 452
          </li>
          <li>
            <svg class="contact-icon" viewBox="0 0 20 20" aria-hidden="true"><path d="M4 2.5 L7.5 2.5 L8.5 6.5 L6.5 8 C7.5 10.5 9.5 12.5 12 13.5 L13.5 11.5 L17.5 12.5 L17.5 16 C17.5 17 16.5 17.5 15.5 17.5 C8.5 17 3 11.5 2.5 4.5 C2.5 3.5 3 2.5 4 2.5 Z"/></svg>
            +40 268 590 126
          </li>
          <li>
            <svg class="contact-icon" viewBox="0 0 20 20" aria-hidden="true"><rect x="1.5" y="4" width="17" height="12"/><polyline points="1.5,4 10,11 18.5,4"/></svg>
            info@drternisu.ro
          </li>
          <li>
            <svg class="contact-icon" viewBox="0 0 20 20" aria-hidden="true"><circle cx="10" cy="10" r="8"/><ellipse cx="10" cy="10" rx="3.5" ry="8"/><line x1="2" y1="10" x2="18" y2="10"/></svg>
            www.drternisu.ro
          </li>
        </ul>
      </div>
    </div>
  </div>
</body>
</html>
```